Kitchen and custom cabinetry company looking for business card design

We make: * Custom Kitchens, contemporary and traditional kitchens, Vanities, Libraries, Custom Entry Doors, Custom Wine Cellars and Custom Design Furniture. Phone number 555-284-7716. Address: Westhampton NY. Email: KAVRO@mailbox.example Portfolio at: KAVROcabinetry.example I would like moderns fonts and not heavy lines. double side but maybe will use clear plastic. I attached the logo.

Industry/Entity Type

Business

```html
<!DOCTYPE html>
<html lang="en">
<head>
<meta charset="utf-8">
<title>KAVRO Cabinetry Inc. – Business Card</title>
<link rel="stylesheet" href="https://fonts.googleapis.com/css2?family=Alegreya:wght@700&family=Cinzel:wght@700&family=Marcellus&family=Open+Sans:wght@400&display=swap">
<style>
  :root {
    --orange: #f15a29;
    --grey: #808080;
    --white: #ffffff;
    --backdrop: #ebe7e0;
    --card-radius: 23px;
  }
  html, body {
    margin: 0;
    padding: 0;
    width: 1200px;
    height: 970px;
    overflow: hidden;
    background: var(--backdrop);
  }
  .canvas {
    position: relative;
    width: 1200px;
    height: 970px;
  }
  .card {
    position: absolute;
    top: 125px;
    width: 408px;
    height: 715px;
    border-radius: var(--card-radius);
    overflow: hidden;
    display: flex;
    flex-direction: column;
    box-shadow: 0 6px 18px rgba(0,0,0,0.12);
  }
  .card--front { left: 175px; }
  .card--back { left: 640px; }

  .band { flex: none; }
  .band--cap { height: 30px; }
  .band--thin { height: 26px; }
  .band--wide { height: 48px; }
  .band--slim { height: 23px; }
  .band--orange { background: var(--orange); }
  .band--grey { background: var(--grey); }

  .brand-panel {
    flex: none;
    height: 268px;
    background: var(--white);
    display: flex;
    flex-direction: column;
    align-items: center;
    padding-top: 72px;
    box-sizing: border-box;
  }
  .brand-name {
    font-family: "Marcellus", serif;
    font-weight: 400;
    color: var(--grey);
    text-align: center;
    line-height: 1;
    margin: 0;
  }
  .brand-name__main {
    display: block;
    font-size: 78px;
    letter-spacing: 4px;
  }
  .brand-name__sub {
    display: block;
    font-size: 19px;
    letter-spacing: 6px;
    margin-top: 6px;
  }

  .info-panel {
    flex: 1;
    color: var(--white);
    text-align: center;
    box-sizing: border-box;
  }
  .info-panel--orange { background: var(--orange); }
  .info-panel--grey { background: var(--grey); }

  .contact { padding-top: 50px; }
  .contact__name {
    font-family: "Alegreya", serif;
    font-weight: 700;
    font-size: 21px;
    margin: 0;
    line-height: 24px;
  }
  .contact__role {
    font-family: "Open Sans", sans-serif;
    font-size: 15px;
    line-height: 20px;
    margin: 0 0 24px;
  }
  .contact__address,
  .contact__lines {
    font-family: "Marcellus", serif;
    font-size: 17px;
    line-height: 20.5px;
    margin: 0;
    font-style: normal;
  }
  .contact__lines { margin-top: 35px; }

  .specialties { padding-top: 76px; }
  .specialties__title {
    font-family: "Cinzel", serif;
    font-weight: 700;
    font-size: 21px;
    letter-spacing: 0.5px;
    margin: 0 0 18px;
  }
  .specialties__list {
    list-style: none;
    margin: 0;
    padding: 0;
    font-family: "Marcellus", serif;
    font-size: 16px;
    line-height: 20.5px;
    text-transform: uppercase;
  }
</style>
</head>
<body>
<main class="canvas">

  <section class="card card--front" aria-label="Card front">
    <div class="band band--cap band--orange"></div>
    <header class="brand-panel">
      <p class="brand-name"><span class="brand-name__main">KAVRO</span><span class="brand-name__sub">CABINETRY INC.</span></p>
    </header>
    <div class="band band--thin band--grey"></div>
    <div class="band band--wide band--orange"></div>
    <div class="band band--slim band--grey"></div>
    <div class="info-panel info-panel--orange contact">
      <h1 class="contact__name">Mateo Lindqvist</h1>
      <p class="contact__role">Owner</p>
      <address class="contact__address">2290 Dune Hollow rd,<br>Westhampton, NY, 11900</address>
      <p class="contact__lines">555-284-7716<br>KAVRO@mailbox.example<br>www.KAVROcabinetry.example</p>
    </div>
  </section>

  <section class="card card--back" aria-label="Card back">
    <div class="band band--cap band--grey"></div>
    <header class="brand-panel">
      <p class="brand-name"><span class="brand-name__main">KAVRO</span><span class="brand-name__sub">CABINETRY INC.</span></p>
    </header>
    <div class="band band--thin band--orange"></div>
    <div class="band band--wide band--grey"></div>
    <div class="band band--slim band--orange"></div>
    <div class="info-panel info-panel--grey specialties">
      <h2 class="specialties__title">OUR SPECIALTIES</h2>
      <ul class="specialties__list">
        <li>Contemporary Kitchens</li>
        <li>Traditional Kitchens</li>
        <li>Vanities</li>
        <li>Libraries</li>
        <li>Custom Wine Cellars</li>
        <li>Custom Design Furniture</li>
      </ul>
    </div>
  </section>

</main>
</body>
</html>
```